Pinecrest Valley Outfitters Banner

We are looking for a banner ad that we will run on DailyLarkPost.com the size is 758x120 and also a matching one that is 300x250 can be animated or static.final graphics will need to be submitted in jpg, gif or similar format. Our shop is a firearms business called "Pinecrest Valley Outfitters" located at 417 Route 52 South, Bramwell Ms. 39247 phone is 662-574-3168 . it need to be modern and eye catching and be more geared to the tactical side. Our website is
pinecrestvoutfitters.com the banners DO NOT have to match website. would like a DIFFERENT LOOK than my website

```html
<!DOCTYPE html>
<html lang="en">
<head>
<meta charset="utf-8">
<title>Pinecrest Valley Outfitters Banner</title>
<link rel="stylesheet" href="https://fonts.googleapis.com/css2?family=Cinzel:wght@900&family=Roboto:wght@500;700&display=swap">
<style>
  :root {
    --frame: #2c2c2c;
    --steel-dark: #17181a;
    --steel-mid: #3e4043;
    --steel-light: #9a9da1;
    --headline-red: #b8141c;
    --white: #ffffff;
    --call-blue: #123f8a;
    --call-blue-light: #1f5dbd;
    --brand-mark: #e0a81c;
  }
  * { margin: 0; padding: 0; box-sizing: border-box; }
  html, body {
    width: 1200px;
    height: 190px;
    overflow: hidden;
    background: var(--white);
  }
  .banner {
    position: relative;
    width: 1200px;
    height: 190px;
    border: 2px solid var(--frame);
    overflow: hidden;
    font-family: "Roboto", Arial, sans-serif;
  }
  .banner__photo {
    position: absolute;
    inset: 0;
    background:
      radial-gradient(ellipse 420px 150px at 820px 60px, var(--steel-light) 0%, rgba(154,157,161,0) 75%),
      radial-gradient(ellipse 260px 120px at 330px 95px, #5a5c60 0%, rgba(90,92,96,0) 80%),
      linear-gradient(100deg, var(--steel-dark) 0%, var(--steel-mid) 40%, #73767a 65%, #2a2b2e 100%);
  }
  .brand {
    position: absolute;
    left: 12px;
    top: 12px;
    display: flex;
    align-items: center;
    gap: 14px;
  }
  .brand__mark {
    flex: none;
    width: 78px;
    height: 86px;
    background: var(--brand-mark);
  }
  .brand__name {
    color: var(--white);
    font-weight: 700;
    font-size: 24px;
    line-height: 1.15;
  }
  .headline {
    position: absolute;
    left: 400px;
    top: 30px;
    width: 440px;
    font-family: "Cinzel", Georgia, serif;
    font-weight: 900;
    font-size: 42px;
    line-height: 62px;
    color: var(--headline-red);
    white-space: nowrap;
    text-shadow:
      -2px -2px 0 var(--white), 2px -2px 0 var(--white),
      -2px 2px 0 var(--white), 2px 2px 0 var(--white),
      0 2px 0 var(--white), 2px 0 0 var(--white),
      0 -2px 0 var(--white), -2px 0 0 var(--white),
      3px 4px 3px rgba(0,0,0,0.6);
  }
  .headline__line { display: block; }
  .headline__line--second { margin-left: -8px; }
  .call {
    position: absolute;
    left: 936px;
    top: 36px;
    width: 252px;
    height: 66px;
    background: linear-gradient(180deg, var(--call-blue-light), var(--call-blue));
    border: 2px solid var(--white);
    border-radius: 8px;
  }
  .call__icon {
    position: absolute;
    left: -14px;
    top: -8px;
    width: 78px;
    height: 78px;
  }
  .call__text {
    position: absolute;
    left: 74px;
    right: 6px;
    top: 6px;
    color: var(--white);
    text-align: center;
  }
  .call__label {
    display: block;
    font-size: 18px;
    font-weight: 500;
    line-height: 24px;
  }
  .call__number {
    display: block;
    margin-top: 4px;
    font-size: 17px;
    font-weight: 500;
    line-height: 24px;
  }
</style>
</head>
<body>
  <div class="banner">
    <div class="banner__photo" role="img" aria-label="Close-up photograph of a stainless steel pistol slide and grip in dark grey tones"></div>

    <div class="brand">
      <span class="brand__mark"></span>
      <span class="brand__name">Pinecrest Valley<br>Outfitters</span>
    </div>

    <h1 class="headline">
      <span class="headline__line">Firearms, Ammo</span>
      <span class="headline__line headline__line--second">and Accessories</span>
    </h1>

    <div class="call">
      <svg class="call__icon" viewBox="0 0 94 94" aria-hidden="true">
        <circle cx="47" cy="47" r="44" fill="#ffffff" stroke="#123f8a" stroke-width="4"/>
        <path d="M33 26c3-1 5 0 6 3l3 8c1 2 0 4-2 5l-3 2c2 6 7 11 13 14l2-3c1-2 3-3 5-2l8 3c3 1 4 3 3 6l-2 5c-1 3-4 4-7 4-18-2-33-17-35-35 0-3 1-6 4-7z" fill="#123f8a"/>
        <path d="M55 30a12 12 0 0 1 10 10M57 22a20 20 0 0 1 16 16M59 14a28 28 0 0 1 22 22" fill="none" stroke="#123f8a" stroke-width="3.5" stroke-linecap="round"/>
      </svg>
      <div class="call__text">
        <span class="call__label">Call Toll Free:</span>
        <span class="call__number">662-574-3168</span>
      </div>
    </div>
  </div>
</body>
</html>
```